San Francisco Leading Consulting firm - 47Vora Web Design Project

•Create a Web Design
•Uncoded webpage layout design
•2 Pages Design - Homepage + Interior Page

Task Description
Hello, we're looking for a re-design our current website www.47vora-example.com

we have a sample mockup design @

http://47vora.pubtrellis-example.org/

This shows the layout that we like and also a sample of 6 pictures that would change based on where you mouse over..

6 pictures HOME design needs to be included.

SMART
THOUGHTFUL
FLEXIBLE
CREATIVE SERVICES
TECHNICAL SERVICES
PARTNERS

sites we like:

http://www.melvanadvisory-example.com/Home.cfm?id=Home
http://www.plinthworks-example.com/index.html

Our company can be best described as: 100+ employees, cutting-edge, depandable, innovative, strong, smart.

Our Primary focus is: IT Consulting Services and Creative Design services

47Vora LLC is a consulting firm providing creative design, business and technology solutions to both private and public interests.

Established in 1996, 47Vora is a San Francisco based company providing specialists for a range of business needs including:

Creative Design Services
•Print
•Logo Design
•Website Design
•Illustration

and

Business and Technology solutions

•Application Software and Web Development
•Business Process Re-Design (BPR)
•Business/Systems Analysis and Requirement Documentation
•Mentoring and Training
•Network/Hardware Installation Services
•System Design and Architecture
•Vendor Management
•Docuvault Architecture and Implementation

our sample mockup site:

Reason: Due to holiday season, we're not available to work with designers and finilize our design.  

Thank you very much for submitting your design.

We appreciate your time and creativity.   Since, our office is currently closed for holidays, we will be reviewing it in details next week and will make our decision as soon as possible.

It would be great if you could submit any of your changes by Wed next week, so it would be part of our reviews. 

Please see updated wireframe under attachments:  we have some minor updates to our wireframe that we would like you to update your designs, if possible.  

We also encorouge you not to use our standard wireframe and come up with more unique designs.   Everything would be considered when we review your design.

 

Target Market(s)

Creative services and professional services clients, including government agencies

Industry/Entity Type

Business

Requirements
Must have
• Clean, professional look, easy navigation

```html
<!DOCTYPE html>
<html lang="en">
<head>
<meta charset="utf-8">
<title>47Vora — Technology Solutions</title>
<link href="https://fonts.googleapis.com/css2?family=Open+Sans:wght@300;400;600;700&display=swap" rel="stylesheet">
<style>
:root{
  --band:#edf0f4;
  --white:#ffffff;
  --ink:#3a3a3a;
  --muted:#6b6b6b;
  --rule:#d6d9dd;
  --cyan:#3fcde6;
  --cyan-deep:#1fb4dc;
  --magenta:#b8168a;
  --orange:#f0a11e;
  --nav-arrow:#f0a11e;
  --button:#7b7b7b;
  --logo:#1f7fc4;
}
*{box-sizing:border-box;margin:0;padding:0}
html,body{width:1057px;height:1200px;overflow:hidden}
body{position:relative;background:var(--white);font-family:"Open Sans",Arial,sans-serif;color:var(--ink)}
.abs{position:absolute}

.header{left:0;top:0;width:1057px;height:100px;background:var(--band)}
.brand{left:113px;top:36px;display:flex;align-items:center;gap:10px;font-size:28px;font-weight:600;color:var(--logo);letter-spacing:1px}
.brand-dot{width:28px;height:28px;border-radius:50%;background:var(--logo)}
.tagline{left:293px;top:48px;font-size:12px;color:#444}
.search{left:813px;top:55px;width:144px;height:21px;background:var(--white);border:1px solid #dde0e4;font-size:8px;font-style:italic;color:#999;padding:5px 7px}
.search svg{position:absolute;right:5px;top:4px}

.intro{left:0;top:100px;width:1057px;height:189px;background:var(--white)}
.nav{left:113px;top:113px;width:154px;list-style:none}
.nav li{height:34px;border-bottom:1px dotted var(--rule);font-size:10px;font-weight:700;letter-spacing:1px;color:#333;line-height:34px}
.nav li:last-child{border-bottom:none}
.nav li span{color:var(--nav-arrow);margin-left:6px;font-weight:700}
.intro-rule{left:287px;top:113px;width:1px;height:122px;background:var(--rule)}
.welcome{left:309px;top:116px;font-size:29px;font-weight:300;color:var(--cyan)}
.intro-text{left:309px;top:162px;width:630px;font-size:11.5px;line-height:21px;color:#444}
.intro-text p{margin-bottom:12px}

.gallery{left:0;top:289px;width:1057px;height:302px;background:var(--band)}
.thumbs{left:157px;top:295px;width:80px}
.thumb{width:80px;height:45px;margin-bottom:4px;border:2px solid #fff}
.pointer{left:256px;top:361px}
.feature{left:264px;top:289px;width:688px;height:302px;display:flex}
.shot-a{width:301px;height:100%;background:linear-gradient(135deg,#b8b4ae,#e6e4e0 55%,#9a9690)}
.shot-b{width:195px;height:100%;background:linear-gradient(160deg,#d9dadc,#8d9196 60%,#4c5055);border-left:1px solid #fff}
.shot-c{width:192px;height:100%;background:linear-gradient(180deg,#f4f4f4,#e3dcd6);border-left:1px solid #fff}
.caption{left:264px;top:513px;width:296px;height:60px;background:rgba(255,255,255,.85);display:flex;align-items:center;padding-left:18px;gap:12px;font-size:34px;font-weight:300;color:#111}

.col{top:631px;width:276px;height:286px;border-left:1px dashed #c8c8c8;padding-left:20px}
.col-label{font-size:13.5px;color:#666;margin-top:4px}
.col-title{font-size:17px;font-weight:700;letter-spacing:.5px;margin-top:14px}
.col-media{margin-top:12px;height:80px}
.col-text{position:absolute;left:20px;top:170px;font-size:11px;line-height:19px;color:#444;width:262px}
.btn{position:absolute;left:20px;top:251px;width:76px;height:29px;border-radius:4px;background:var(--button);color:#fff;font-size:11.5px;text-align:center;line-height:29px}
.col-notch{position:absolute;left:-1px;top:8px}

.services{left:64px;top:960px;width:888px;height:193px;background:var(--white);box-shadow:0 -8px 12px -8px rgba(0,0,0,.12),0 8px 12px -8px rgba(0,0,0,.12)}
.svc-title{font-size:13px;font-weight:700;color:#333}
.svc-list{list-style:none;font-size:10px;color:#333}
.svc-list li{position:relative;padding-left:8px;margin-bottom:11px;line-height:13px}
.svc-list li::before{content:"•";position:absolute;left:0}
.svc-rule{left:369px;top:983px;width:1px;height:154px;background:var(--rule)}
.copyright{left:0;top:1171px;width:1040px;text-align:center;font-size:10px;color:#222}
</style>
</head>
<body>

<header class="abs header"></header>
<div class="abs brand"><span class="brand-dot"></span>47VORA</div>
<div class="abs tagline">Thechnology Solutions for the 21st Century</div>
<div class="abs search">SEARCH
  <svg width="12" height="12" viewBox="0 0 12 12"><circle cx="7" cy="5" r="3.5" fill="none" stroke="#f0a11e" stroke-width="1.5"/><line x1="4.5" y1="7.5" x2="1" y2="11" stroke="#f0a11e" stroke-width="1.8"/></svg>
</div>

<section class="abs intro"></section>
<ul class="abs nav">
  <li>COMPANY<span>›</span></li>
  <li>TECHNICAL SERVICES<span>›</span></li>
  <li>CREATIVE SERVICES<span>›</span></li>
  <li>PARTNERS<span>›</span></li>
  <li>CONTACT US</li>
</ul>
<div class="abs intro-rule"></div>
<h1 class="abs welcome">welcome</h1>
<div class="abs intro-text">
  <p>47Vora LLC is a consulting firm providing creative design, business and technology solutions to both private and public interests.</p>
  <p>Our experts possess broad industry knowledge which can help with technical and businessprocess challenges, delivering solutions that are creative and cost effective.</p>
</div>

<section class="abs gallery"></section>
<div class="abs thumbs">
  <div class="thumb" role="img" aria-label="Thumbnail: hands holding a heart" style="background:linear-gradient(135deg,#9fb4c4,#d9c9c6)"></div>
  <div class="thumb" role="img" aria-label="Thumbnail: colleagues reviewing work" style="background:linear-gradient(135deg,#a8a6a2,#dcdad6)"></div>
  <div class="thumb" role="img" aria-label="Thumbnail: person at a laptop" style="background:linear-gradient(135deg,#cfd3d6,#9ea5aa)"></div>
  <div class="thumb" role="img" aria-label="Thumbnail: colourful design swatches" style="background:linear-gradient(135deg,#8fa29a,#c9b48a,#a37eb0)"></div>
  <div class="thumb" role="img" aria-label="Thumbnail: business team" style="background:linear-gradient(135deg,#b9bcc2,#8e929a)"></div>
  <div class="thumb" role="img" aria-label="Thumbnail: handshake" style="background:linear-gradient(135deg,#d8d2c8,#b7aa98)"></div>
</div>
<svg class="abs pointer" width="8" height="14" viewBox="0 0 8 14"><polygon points="8,0 0,7 8,14" fill="#5a6570"/></svg>
<div class="abs feature">
  <div class="shot-a" role="img" aria-label="Photo: two colleagues reviewing work together"></div>
  <div class="shot-b" role="img" aria-label="Photo: hands typing on a keyboard"></div>
  <div class="shot-c" role="img" aria-label="Photo: hand drawing a flowchart"></div>
</div>
<div class="abs caption">
  <svg width="14" height="26" viewBox="0 0 14 26"><polyline points="2,2 12,13 2,24" fill="none" stroke="#3fcde6" stroke-width="4"/></svg>
  thoughtful
</div>

<article class="abs col" style="left:107px">
  <svg class="col-notch" width="6" height="12" viewBox="0 0 6 12"><polyline points="0,0 6,6 0,12" fill="#fff" stroke="#c8c8c8"/></svg>
  <div class="col-label">for graphic designers</div>
  <h2 class="col-title" style="color:var(--magenta)">GET CREATIVE !</h2>
  <div class="col-media" role="img" aria-label="Illustration: colourful creative swirl" style="width:225px;background:linear-gradient(90deg,#8a2c9c,#d8286a 45%,#f6c1cf 80%,#fff)"></div>
  <p class="col-text">47Vora is looking for top creative talent to deliver graphic design solutions for some leading global brands Do you have what it takes?</p>
  <div class="btn">Learn More</div>
</article>

<article class="abs col" style="left:383px">
  <svg class="col-notch" width="6" height="12" viewBox="0 0 6 12"><polyline points="0,0 6,6 0,12" fill="#fff" stroke="#c8c8c8"/></svg>
  <div class="col-label">for clients</div>
  <h2 class="col-title" style="color:var(--orange)">THE 47VORA DIFFERENCE</h2>
  <div class="col-media" role="img" aria-label="Illustration: figure with briefcase racing ahead" style="width:256px;background:linear-gradient(90deg,#cfcfd1,#b9b8bb 50%,#c9c8cb)"></div>
  <p class="col-text">Smart, Flexible, Thoughtful: find out why leading corporations and government agencies are turning to 47Vora to help manage their most demanding IT services challenges.</p>
  <div class="btn">Learn More</div>
</article>

<article class="abs col" style="left:672px">
  <svg class="col-notch" width="6" height="12" viewBox="0 0 6 12"><polyline points="0,0 6,6 0,12" fill="#fff" stroke="#c8c8c8"/></svg>
  <div class="col-label">for partners</div>
  <h2 class="col-title" style="color:var(--cyan-deep)">TEAM UP WITH THE BEST</h2>
  <div class="col-media" role="img" aria-label="Photo: business handshake" style="width:256px;background:linear-gradient(90deg,#3a3d42,#8b8f96 45%,#c9ccd0 60%,#2f3236)"></div>
  <p class="col-text">When it comes to technology partnerships,<br>our mission it so make you a success.</p>
  <div class="btn">Learn More</div>
</article>

<section class="abs services"></section>
<h3 class="abs svc-title" style="left:108px;top:993px">Creative Design Services</h3>
<ul class="abs svc-list" style="left:123px;top:1026px;width:200px">
  <li>Print</li><li>Logo Design</li><li>Website Design</li><li>Illustration</li>
</ul>
<div class="abs svc-rule"></div>
<h3 class="abs svc-title" style="left:415px;top:993px">Business and Technology solutions</h3>
<ul class="abs svc-list" style="left:429px;top:1026px;width:230px">
  <li>Application Software and Web Development</li>
  <li>Business Process Re-Design (BPR)</li>
  <li>Business/Systems Analysis and Requirement Documentation</li>
  <li>Mentoring and Training</li>
</ul>
<ul class="abs svc-list" style="left:680px;top:1026px;width:240px">
  <li>Network/Hardware Installation Services</li>
  <li>System Design and Architecture</li>
  <li>Vendor Management</li>
  <li>Docuvault Architecture and Implementation</li>
</ul>

<footer class="abs copyright">Copyright 2010, 47Vora, LLC All rights reserved.</footer>

</body>
</html>
```